Mayhon online ordering platform looking for a great web design

Mayhon - from the Vietnamese words Mây Hồng meaning financial success.
Background
Mayhon is an online ordering platform for small retail businesses (corner stores). The idea is that small retailers will use the website to order their supplies. From this we will utilise the group buying to get better deals for them that they could not achieve individually.
We are looking for a simple but stylish design for our ordering page. The layout needs to be efficient, logical and self explanatory.
Products to be sold on the site are FMCG (fast moving consumer goods). Potential to be 000's of items.
Considerations
- end users are not technologically adept.
- Users are generally older so small print will not be well received.
- Use of touch screen monitors to select/change items so spacing in design is vital.
- Logical display of category and sub-categories.
- Easy selection of products to order as well as modification of quantity.
- Shopping cart with easy change of item quantity.
- List of items for ordering can be paginated.
- Items listed will have image for easy identification.
- Search box
- Format should be in psd (photoshop) or complete html/css
- All this information needs to be displayed on the one page.
Product information to contain the following:
- Image
- Price
- Product name
- Size
Area for prominent display of specials without crowding the product information.

```html
<!DOCTYPE html>
<html lang="en">
<head>
<meta charset="utf-8">
<title>Mayhon – Sub Category</title>
<link href="https://fonts.googleapis.com/css2?family=Ubuntu:wght@400;500;700&family=Oswald:wght@600&display=swap" rel="stylesheet">
<style>
:root{
  --orange:#f15a2b;
  --orange-dark:#d9431a;
  --teal:#13b6c4;
  --ink:#333;
  --muted:#8a8a8a;
  --line:#dcdcdc;
  --bar:#f2eee4;
  --footer:#ebebeb;
  --black:#0e0e0e;
}
*{box-sizing:border-box;margin:0;padding:0}
html,body{width:900px;height:1200px;overflow:hidden;background:#fff;font-family:"Ubuntu",sans-serif;color:var(--ink)}
.page{position:relative;width:900px;height:1200px}
.topbar{position:absolute;left:0;top:0;width:900px;height:26px;background:var(--black);color:#fff;font-size:9px;font-weight:500}
.topbar span{position:absolute;top:8px}
.logo{position:absolute;left:96px;top:50px;font-size:22px;color:#8b8b8b;letter-spacing:.5px}
.bar{position:absolute;left:97px;width:705px;height:25px;background:var(--bar);border:1px solid #ddd8cc}
.nav{top:102px}
.nav a{position:absolute;top:6px;font-size:10px;color:#444;text-decoration:none}
.nav .home{left:-1px;top:-1px;width:74px;height:25px;background:var(--orange);color:#fff;font-weight:500;font-size:11px;text-align:center;line-height:25px;border:1px solid var(--orange-dark)}
.field{position:absolute;right:3px;top:3px;width:158px;height:18px;background:#fff;border:1px solid #ddd;font-size:9px;font-style:italic;color:#777;padding:3px 8px}
.banner{position:absolute;left:97px;top:131px;width:705px;height:145px;border:1px solid var(--line);padding:4px}
.banner-inner{position:relative;width:100%;height:100%;background:var(--teal);overflow:hidden}
.banner-photo{position:absolute;left:0;top:0;width:200px;height:100%;background:linear-gradient(90deg,#e9dcd2,#f4f1ee 60%,#d8c9c0)}
.deal{position:absolute;left:340px;top:18px;font-family:"Oswald",sans-serif;font-weight:600;color:#fff;font-size:82px;line-height:1;letter-spacing:-1px}
.upto{position:absolute;left:300px;top:95px;transform:rotate(-90deg);transform-origin:left top;font-family:"Oswald",sans-serif;font-weight:600;color:#fff;font-size:30px;line-height:1}
.btn{position:absolute;background:#f7f4ee;border:1px solid #d7d2c6;font-size:9px;color:#555;text-align:center}
.catbar{top:283px}
.drop{position:absolute;top:-1px;height:25px;width:134px;border-right:1px solid #ddd8cc;font-size:10px;padding:8px 10px;color:#444}
.drop::after{content:"";position:absolute;right:8px;top:11px;border:3px solid transparent;border-top-color:currentColor}
.drop.active{background:var(--orange);color:#fff;font-weight:500;border:1px solid var(--orange-dark)}
.crumb{position:absolute;left:97px;top:318px;font-size:8px;color:#444}
.crumb em{font-style:normal;color:var(--orange)}
.title{position:absolute;left:97px;top:330px;font-size:20px;font-weight:700;color:var(--orange)}
.panel{position:absolute;left:97px;width:705px;border:1px solid var(--line)}
.panel h2{font-weight:400;font-size:13px;color:var(--orange);margin:7px 8px 0;padding-bottom:6px;border-bottom:1px solid var(--line);width:689px}
.panel h2 small{font-size:8px;color:#444}
.row{display:flex;margin:0 8px;border-bottom:1px solid var(--line);height:178px}
.row.last{border-bottom:1px solid var(--line)}
.product{position:relative;flex:1;border-right:1px solid var(--line);margin:9px 0}
.product:last-child{border-right:none}
.shot{position:absolute;left:50%;top:0;width:44px;height:126px;margin-left:-22px;border-radius:12px 12px 6px 6px}
.green{background:linear-gradient(#4cc63c,#2e9f2a)}
.blue{background:linear-gradient(90deg,#f2f2f2,#fff 60%,#1e4fb0)}
.white{background:linear-gradient(90deg,#dcdcdc,#fafafa 50%,#d5d5d5)}
.pink{background:linear-gradient(#ee3d78,#c71a55)}
.name{position:absolute;left:18px;top:134px;font-size:9px;font-weight:500;color:var(--orange)}
.size,.price{position:absolute;top:147px;font-size:9px;color:#444}
.size{left:18px}.price{right:18px}
.pager{position:absolute;left:8px;top:393px;display:flex;gap:3px;font-size:8px;color:#bbb}
.pager span{border:1px solid #ddd;height:13px;line-height:11px;padding:0 4px}
.pager .on{border-color:var(--orange);color:var(--orange)}
.perpage{position:absolute;right:9px;top:393px;font-size:8px;color:#999}
.perpage span{border:1px solid #ddd;padding:1px 4px;margin-left:6px}
.footer{position:absolute;left:0;top:1013px;width:900px;height:187px;background:var(--footer);font-size:8.5px;color:#999}
.col{position:absolute;top:26px}
.col h3{font-size:8.5px;font-weight:400;color:#333;margin-bottom:5px}
.col p{line-height:15.6px}
.news{position:absolute;left:636px;top:43px;width:165px;height:18px;border:1px solid #bbb;border-radius:9px;background:#fff;padding:3px 9px;color:#888}
.news i{position:absolute;right:1px;top:1px;width:14px;height:14px;border-radius:50%;background:#2a7fd4}
.social{position:absolute;left:636px;top:89px;display:flex;gap:5px}
.social span{width:22px;height:22px;border-radius:3px;background:#9a9a9a}
.copy{position:absolute;left:97px;top:157px;color:#888}
.copy b{font-weight:400;color:#333}
</style>
</head>
<body>
<div class="page">
  <header class="topbar">
    <span style="left:648px">Register</span>
    <span style="left:704px">Sign Up</span>
    <span style="left:754px">My Cart (2)</span>
  </header>
  <div class="logo">LOGO HERE</div>

  <nav class="bar nav">
    <a class="home">Home</a>
    <a style="left:101px">About</a>
    <a style="left:165px">Categories</a>
    <a style="left:253px">How it works</a>
    <a style="left:351px">Contact Us</a>
    <a style="left:439px">Support</a>
    <div class="field">search</div>
  </nav>

  <section class="banner">
    <div class="banner-inner">
      <div class="banner-photo" role="img" aria-label="Photo of a woman in a white top, hand on hip"></div>
      <div class="upto">UPTO</div>
      <div class="deal">20% OFF</div>
      <div class="btn" style="left:622px;top:110px;width:68px;height:19px;line-height:17px">Learn More</div>
    </div>
  </section>
  <div class="btn" style="left:817px;top:171px;width:68px;height:20px;line-height:18px">Learn More</div>

  <div class="bar catbar">
    <div class="drop" style="left:0">Main Category</div>
    <div class="drop" style="left:134px">Sub Category</div>
    <div class="drop active" style="left:268px;width:135px">Optional Category</div>
    <div class="field">search category</div>
  </div>

  <div class="crumb">Home &gt; Main Category &gt; <em>Sub Category</em></div>
  <h1 class="title">Sub Category</h1>

  <section class="panel" style="top:363px;height:213px">
    <h2>Featured Products</h2>
    <div class="row" style="border-bottom:none">
      <div class="product"><div class="shot green" role="img" aria-label="Green shampoo bottle"></div><div class="name">Product Name</div><div class="size">500ml</div><div class="price">$2.59</div></div>
      <div class="product"><div class="shot blue" role="img" aria-label="White and blue shampoo bottle"></div><div class="name">Product Name</div><div class="size">500ml</div><div class="price">$2.59</div></div>
      <div class="product"><div class="shot white" role="img" aria-label="White shampoo bottle"></div><div class="name">Product Name</div><div class="size">500ml</div><div class="price">$2.59</div></div>
      <div class="product"><div class="shot white" role="img" aria-label="White shampoo bottle"></div><div class="name">Product Name</div><div class="size">500ml</div><div class="price">$2.59</div></div>
      <div class="product"><div class="shot pink" role="img" aria-label="Pink shampoo bottle"></div><div class="name">Product Name</div><div class="size">500ml</div><div class="price">$2.59</div></div>
    </div>
  </section>

  <section class="panel" style="top:581px;height:418px">
    <h2>Latest Arrivals <small>(see all)</small></h2>
    <div class="row">
      <div class="product"><div class="shot green" role="img" aria-label="Green shampoo bottle"></div><div class="name">Product Name</div><div class="size">500ml</div><div class="price">$2.59</div></div>
      <div class="product"><div class="shot blue" role="img" aria-label="White and blue shampoo bottle"></div><div class="name">Product Name</div><div class="size">500ml</div><div class="price">$2.59</div></div>
      <div class="product"><div class="shot white" role="img" aria-label="White shampoo bottle"></div><div class="name">Product Name</div><div class="size">500ml</div><div class="price">$2.59</div></div>
      <div class="product"><div class="shot white" role="img" aria-label="White shampoo bottle"></div><div class="name">Product Name</div><div class="size">500ml</div><div class="price">$2.59</div></div>
      <div class="product"><div class="shot pink" role="img" aria-label="Pink shampoo bottle"></div><div class="name">Product Name</div><div class="size">500ml</div><div class="price">$2.59</div></div>
    </div>
    <div class="row">
      <div class="product"><div class="shot green" role="img" aria-label="Green shampoo bottle"></div><div class="name">Product Name</div><div class="size">500ml</div><div class="price">$2.59</div></div>
      <div class="product"><div class="shot blue" role="img" aria-label="White and blue shampoo bottle"></div><div class="name">Product Name</div><div class="size">500ml</div><div class="price">$2.59</div></div>
      <div class="product"><div class="shot white" role="img" aria-label="White shampoo bottle"></div><div class="name">Product Name</div><div class="size">500ml</div><div class="price">$2.59</div></div>
      <div class="product"><div class="shot white" role="img" aria-label="White shampoo bottle"></div><div class="name">Product Name</div><div class="size">500ml</div><div class="price">$2.59</div></div>
      <div class="product"><div class="shot pink" role="img" aria-label="Pink shampoo bottle"></div><div class="name">Product Name</div><div class="size">500ml</div><div class="price">$2.59</div></div>
    </div>
    <div class="pager">
      <span style="width:44px">Previous</span><span class="on">1</span><span>2</span><span>3</span><span>4</span><span>5</span><span style="width:45px;color:#777;text-align:center">Next</span>
    </div>
    <div class="perpage">display per page <span>50 ▾</span></div>
  </section>

  <footer class="footer">
    <div class="col" style="left:97px"><h3>Why Us</h3><p>Features<br>Pricing<br>Site Gallery<br>Demo Video<br>Clients<br>Testimonials</p></div>
    <div class="col" style="left:187px"><h3>Company</h3><p>About Us<br>Press<br>Careers<br>Contact Us<br>Partner with Us</p></div>
    <div class="col" style="left:277px"><h3>Support</h3><p>Help<br>Contact Support<br>Video Tutorials<br>Privacy Policy<br>Terms of Service<br>Report Abuse</p></div>
    <div class="col" style="left:365px"><h3>Community</h3><p>Blog<br>Forums<br>Affiliates</p></div>
    <div class="col" style="left:457px"><h3>Contact Us</h3><p>27-A, Lotus Lane<br>Gravida nibh vel velit auctor aliquet<br>Aenean sollicitudin<br>Riverton<br><br>hello@mayhon-store.com<br>(555) 014 2938</p></div>
    <div class="col" style="left:636px"><h3>Subscribe Newsletter</h3></div>
    <div class="news">email address<i></i></div>
    <div class="col" style="left:636px;top:70px"><h3>Follow Us</h3></div>
    <div class="social"><span></span><span></span><span></span><span></span></div>
    <div class="copy">Copyright 2013. All rights reserved. <b>Privacy Policy</b> | <b>Terms of Service</b></div>
  </footer>
</div>
</body>
</html>
```